Keswyn Capital LLC

Need Professional Business cards for New Investment Fund

Target Market(s)

High Quality investors

Industry/Entity Type

Financial

Contact Information for Business Card

Phone Number +1 555 284 6190
Name Lukas Varenko
Title Fund Manager
email lv@FundCorvel.com
Website www.FundCorvel.com

Colors

Designer to choose colors to be used in the design.

Requirements
Must have
• Must have our Logo and all of the above. Must be made so lettering and loge can be raised

```html
<!DOCTYPE html>
<html lang="en">
<head>
<meta charset="utf-8">
<title>Keswyn Capital LLC — Business Card</title>
<link href="https://fonts.googleapis.com/css2?family=Roboto:wght@400;500;700&display=swap" rel="stylesheet">
<style>
  :root {
    --backdrop: #e3e3e3;
    --paper: #ffffff;
    --brand-green: #22ee00;
    --ink-green: #2ee00f;
    --charcoal: #434a43;
    --text-grey: #4a4a4a;
    --white: #ffffff;
  }
  * { margin: 0; padding: 0; box-sizing: border-box; }
  html, body {
    width: 1200px; height: 1200px; overflow: hidden;
    background: var(--backdrop);
    font-family: "Roboto", Arial, sans-serif;
  }
  .card {
    position: absolute; left: 262px; width: 686px; height: 392px;
  }
  .card--front { top: 165px; background: var(--paper); }
  .card--front .edge-band {
    position: absolute; left: 0; bottom: 0; width: 100%; height: 13px;
    background: var(--charcoal);
  }
  .card--back { top: 653px; background: var(--brand-green); }

  .wordmark {
    position: absolute; display: flex; align-items: center; gap: 10px;
    font-weight: 700; letter-spacing: 1px; white-space: nowrap;
  }
  .wordmark__square { width: 22px; height: 22px; flex: none; }
  .card--front .wordmark {
    right: 404px; top: 178px; font-size: 30px; color: var(--charcoal);
  }
  .card--front .wordmark__square { background: var(--brand-green); }
  .card--back .wordmark {
    left: 0; width: 100%; justify-content: center; top: 176px;
    font-size: 40px; color: var(--white);
  }
  .card--back .wordmark__square { background: var(--white); width: 28px; height: 28px; }

  .divider {
    position: absolute; left: 308px; top: 123px; width: 2px; height: 146px;
    background: var(--charcoal);
  }
  .holder { position: absolute; left: 342px; top: 133px; }
  .holder__name { font-size: 23px; font-weight: 700; color: var(--ink-green); line-height: 1; }
  .holder__title { margin-top: 6px; font-size: 16px; font-weight: 500; color: var(--text-grey); }

  .contacts { position: absolute; left: 342px; top: 195px; list-style: none; }
  .contacts li {
    display: flex; align-items: center; gap: 9px;
    font-size: 15.5px; color: var(--text-grey); height: 20px; white-space: nowrap;
  }
  .contacts svg { width: 13px; height: 13px; fill: var(--brand-green); flex: none; }

  .card--back .site {
    position: absolute; left: 0; width: 100%; top: 347px; text-align: center;
    color: var(--white); font-size: 16px; letter-spacing: 3.5px;
  }
</style>
</head>
<body>
  <section class="card card--front" aria-label="Card front">
    <div class="wordmark"><span class="wordmark__square"></span>KESWYN</div>
    <div class="divider"></div>
    <div class="holder">
      <p class="holder__name">Lukas Varenko</p>
      <p class="holder__title">Fund Manager</p>
    </div>
    <ul class="contacts">
      <li>
        <svg viewBox="0 0 24 24" aria-hidden="true"><path d="M6.6 10.8a15.1 15.1 0 0 0 6.6 6.6l2.2-2.2a1 1 0 0 1 1-.25 11.4 11.4 0 0 0 3.6.57 1 1 0 0 1 1 1V20a1 1 0 0 1-1 1A17 17 0 0 1 3 4a1 1 0 0 1 1-1h3.5a1 1 0 0 1 1 1c0 1.25.2 2.45.57 3.57a1 1 0 0 1-.25 1z"/></svg>
        +1 555 284 6190
      </li>
      <li>
        <svg viewBox="0 0 24 24" aria-hidden="true"><path d="M2 5h20v14H2z M3.5 6.5 12 12.5l8.5-6z" fill-rule="evenodd"/></svg>
        lv@FundCorvel.com
      </li>
      <li>
        <svg viewBox="0 0 24 24" aria-hidden="true"><circle cx="12" cy="12" r="10"/></svg>
        www.FundCorvel.com
      </li>
    </ul>
    <div class="edge-band"></div>
  </section>

  <section class="card card--back" aria-label="Card back">
    <div class="wordmark"><span class="wordmark__square"></span>KESWYN</div>
    <p class="site">www.FundCorvel.com</p>
  </section>
</body>
</html>
```